Merrow Trade finance web design

We are a newly established business which provides invoice finance to Small Businesses in England and Wales.
Our approach is very much a funder where the small business owner can talk to the decision maker. We will guarantee on receipt of information, a decision within 24 hours.
We are not a bank so the look of the website need to be friendly but professional.
Have two types of people we are trying to attract to the website: 1) partners who are small business owners and 2) introducers who is accountants and commercial brokers who introduce us to the small businesses.
Currently no website, although domain has been reserved.
The design should be:
Professional
“Clean” Look
Designed to convey Trust and Authority.
Appeal to the small business owner.
Must incorporate:
Logo (attached)
Front page:Top tabs to other pages 1) About us 2) Services 3) Introducers 4) Contact us
Need picture and logo on page.
1) About us page- Room for talk about the company, the people and our critera.
2) Services page- We need for what invoice finance is, and 5 boxes for different services we will provide. (link on page to contact us)
3) Introducers page- We need a part for why become an introducer? Who we can help? Why we are different? (link on page to contact us)
4) Contact us page- Office address, email, tel and if possible a map and a contact me part which will email direct to us.
Text will be provided for the design, if we can see the setup of the website we will provide a part for each of the pages to support.
Styles we think convey the correct image:
www.dornelcapital.example
www.plivanlend.example
www.quorbacredit.example
Target Market(s)
Small business owners
Industry/Entity Type
Finance
Number of Pages Required
5+ page
Look and feel

```html
<!DOCTYPE html>
<html lang="en">
<head>
<meta charset="utf-8">
<title>Merrow Trade finance</title>
<link href="https://fonts.googleapis.com/css2?family=PT+Sans:ital,wght@0,400;0,700;1,400&display=swap" rel="stylesheet">
<style>
  :root {
    --red: #b8121c;
    --red-deep: #8e0c13;
    --ink: #1d1d1d;
    --text: #5b5b5b;
    --muted: #8c8c8c;
    --dark: #141414;
    --white: #ffffff;
    --grey-btn: #5c5c52;
  }
  * { box-sizing: border-box; margin: 0; padding: 0; }
  html, body { width: 1200px; height: 2628px; overflow: hidden; }
  body { position: relative; background: var(--white); font-family: "PT Sans", Arial, sans-serif; color: var(--text); }
  .abs { position: absolute; }

  /* Hero */
  .hero { position: absolute; left: 0; top: 0; width: 1200px; height: 640px; overflow: hidden; }
  .hero-photo { position: absolute; inset: 0; background: linear-gradient(100deg, #7a6a5c 0%, #c9a27a 40%, #b98e5e 65%, #e7e4e0 85%, #cfd6dc 100%); }
  .hero svg { position: absolute; left: 0; top: 0; }
  .brand { position: absolute; left: 201px; top: 56px; color: var(--white); font-size: 28px; font-weight: 700; letter-spacing: 0.3px; display: flex; align-items: center; gap: 10px; }
  .brand .dot { width: 14px; height: 14px; border-radius: 50%; background: var(--white); }
  .main-nav { position: absolute; left: 662px; top: 74px; display: flex; gap: 22px; }
  .main-nav a { color: var(--white); text-decoration: none; font-size: 14px; padding-bottom: 14px; }
  .main-nav a.active { border-bottom: 2px solid var(--red); }
  .hero-title { position: absolute; left: 207px; top: 286px; width: 420px; color: var(--white); font-style: italic; font-size: 29px; line-height: 29px; }
  .btn { display: inline-block; background: #0a0a0a; color: var(--white); font-size: 13px; font-weight: 700; text-align: center; border-radius: 8px; text-decoration: none; }
  .hero .btn { position: absolute; left: 201px; top: 448px; width: 152px; height: 44px; line-height: 44px; }
  .slide-btn { position: absolute; top: 456px; width: 52px; height: 28px; border-radius: 14px; }
  .slide-btn.prev { left: 892px; background: var(--grey-btn); }
  .slide-btn.next { left: 950px; background: var(--red); }
  .slide-btn svg { position: absolute; left: 20px; top: 8px; }

  /* Section titles */
  .section-title { position: absolute; left: 0; width: 1200px; text-align: center; font-size: 27px; color: var(--red); }
  .section-title.light { color: var(--white); }
  .swoosh { position: absolute; left: 508px; width: 184px; height: 16px; }

  /* Services */
  .service { position: absolute; width: 260px; }
  .service-head { display: flex; align-items: center; gap: 12px; }
  .service-icon { width: 70px; height: 70px; border-radius: 50%; flex: none; }
  .service-name { font-size: 13.5px; line-height: 17px; color: #555; }
  .service-text { margin-top: 18px; font-size: 10.5px; line-height: 17.5px; color: #6a6a6a; }

  /* Introducers */
  .introducers { position: absolute; left: 0; top: 1160px; width: 1200px; height: 740px; overflow: hidden; }
  .intro-photo { position: absolute; inset: 0; background: linear-gradient(90deg, #a50f18 0%, #bb1520 45%, #96121a 75%, #5e0a10 100%); }
  .introducers svg.edges { position: absolute; left: 0; top: 0; }
  .video-frame { position: absolute; left: 270px; top: 186px; width: 660px; height: 294px; border: 4px solid #e8e8e8; background: linear-gradient(90deg, #5a5a5a, #9a9a9a 45%, #6e6e6e); }
  .play { position: absolute; left: 290px; top: 108px; width: 72px; height: 72px; border: 3px solid var(--white); border-radius: 50%; }
  .play svg { position: absolute; left: 24px; top: 18px; }
  .intro-caption { position: absolute; left: 270px; top: 506px; width: 660px; text-align: center; color: var(--white); font-size: 17px; line-height: 26px; }
  .introducers .btn { position: absolute; left: 525px; top: 574px; width: 150px; height: 44px; line-height: 44px; }

  /* Testimonials */
  .quote-mark { position: absolute; left: 0; top: 1940px; width: 1200px; text-align: center; font-size: 72px; font-weight: 700; color: var(--ink); line-height: 72px; }
  .testimonial-text { position: absolute; left: 240px; top: 2018px; width: 720px; text-align: center; font-size: 17px; line-height: 28px; color: var(--muted); }
  .tri { position: absolute; top: 2078px; }
  .divider { position: absolute; left: 394px; top: 2137px; width: 412px; height: 1px; background: #dcdcdc; }
  .avatar { position: absolute; left: 464px; top: 2158px; width: 76px; height: 76px; border-radius: 50%; border: 3px solid #e4e4e4; background: linear-gradient(180deg, #c9ccd2, #8f96a3); }
  .author { position: absolute; left: 554px; top: 2174px; }
  .author-name { font-size: 17px; color: #333; }
  .author-company { font-size: 10px; color: var(--muted); margin-top: 4px; }

  /* Footer */
  .site-footer { position: absolute; left: 0; top: 2230px; width: 1200px; height: 398px; overflow: hidden; }
  .footer-bg { position: absolute; inset: 0; background: linear-gradient(180deg, #1e1e1e, #101010); }
  .site-footer svg.edge { position: absolute; left: 0; top: 0; }
  .footer-brand { position: absolute; left: 201px; top: 136px; color: var(--white); font-size: 22px; font-weight: 700; display: flex; align-items: center; gap: 8px; }
  .footer-brand .dot { width: 11px; height: 11px; border-radius: 50%; background: var(--white); }
  .social { position: absolute; left: 199px; top: 185px; display: flex; gap: 5px; }
  .social span { width: 24px; height: 24px; border-radius: 50%; }
  .foot-col { position: absolute; top: 128px; }
  .foot-col h4 { color: var(--white); font-size: 13px; font-weight: 700; letter-spacing: 0.3px; }
  .foot-col h4 em { font-style: normal; color: var(--red); }
  .foot-col ul { list-style: none; margin-top: 24px; }
  .foot-col li { font-size: 11px; color: #d8d8d8; height: 27px; padding-left: 21px; position: relative; }
  .foot-col li::before { content: "›"; position: absolute; left: 0; top: -2px; color: var(--red); font-size: 13px; }
  .newsletter p { margin-top: 22px; width: 250px; font-size: 11px; line-height: 17px; color: #d8d8d8; }
  .subscribe { display: flex; margin-top: 14px; }
  .subscribe .field { width: 151px; height: 33px; background: var(--white); color: #aaa; font-size: 9.5px; line-height: 33px; padding-left: 8px; }
  .subscribe .go { width: 91px; height: 33px; background: var(--red); color: var(--white); font-size: 10px; font-weight: 700; line-height: 33px; text-align: center; }
  .footer-rule { position: absolute; left: 0; top: 345px; width: 1200px; height: 1px; background: #2e2e2e; }
  .copyright { position: absolute; left: 0; top: 364px; width: 1200px; text-align: center; font-size: 10px; color: #cfcfcf; }
</style>
</head>
<body>

<header class="hero">
  <div class="hero-photo" role="img" aria-label="Photo of an older man with glasses, hand at his face, looking at a laptop screen"></div>
  <svg width="1200" height="640" viewBox="0 0 1200 640" aria-hidden="true">
    <path d="M0 0 H600 C420 40 250 150 0 360 Z" fill="#b8121c" opacity="0.93"/>
    <path d="M520 0 H1200 V22 C980 6 760 6 520 0 Z" fill="#b8121c" opacity="0.9"/>
    <path d="M0 558 C380 600 800 640 1200 606 V640 H0 Z" fill="#ffffff"/>
  </svg>
  <div class="brand"><span class="dot"></span>Merrow Trade finance</div>
  <nav class="main-nav">
    <a class="active" href="#">Home</a>
    <a href="#">About Us</a>
    <a href="#">Services</a>
    <a href="#">Introducers</a>
    <a href="#">Contact Us</a>
  </nav>
  <h1 class="hero-title">We are a new business which provides invoice finance to Small Businesses in England and Wales</h1>
  <a class="btn" href="#">Learn More</a>
  <span class="slide-btn prev"><svg width="10" height="12" viewBox="0 0 10 12"><path d="M7 1 L2 6 L7 11" stroke="#fff" stroke-width="2.2" fill="none"/></svg></span>
  <span class="slide-btn next"><svg width="10" height="12" viewBox="0 0 10 12"><path d="M3 1 L8 6 L3 11" stroke="#fff" stroke-width="2.2" fill="none"/></svg></span>
</header>

<h2 class="section-title" style="top:630px">Our Services</h2>
<svg class="swoosh" style="top:672px" viewBox="0 0 184 16" aria-hidden="true"><path d="M2 14 C60 2 130 0 182 4 C130 4 70 7 2 14 Z" fill="#1d1d1d"/></svg>

<section class="services">
  <div class="service" style="left:201px;top:750px">
    <div class="service-head"><span class="service-icon" role="img" aria-label="Invoice factoring icon" style="background:#7cc84a"></span><span class="service-name">Invoice<br>Factoring</span></div>
    <p class="service-text">Lorem Ipsum is simply dummy text of the printing and typesetting industry. Lorem Ipsum has been the industry's standard dummy text ever since the 1500s, when an unknown printer</p>
  </div>
  <div class="service" style="left:475px;top:750px">
    <div class="service-head"><span class="service-icon" role="img" aria-label="Invoice discounting icon" style="background:#6fc247"></span><span class="service-name">Invoice<br>Discounting</span></div>
    <p class="service-text">Lorem Ipsum is simply dummy text of the printing and typesetting industry. Lorem Ipsum has been the industry's standard dummy text ever since the 1500s, when an unknown printer</p>
  </div>
  <div class="service" style="left:748px;top:750px">
    <div class="service-head"><span class="service-icon" role="img" aria-label="Accounts receivable icon" style="background:#3c4150"></span><span class="service-name">Accounts<br>Receivable</span></div>
    <p class="service-text">Lorem Ipsum is simply dummy text of the printing and typesetting industry. Lorem Ipsum has been the industry's standard dummy text ever since the 1500s, when an unknown printer</p>
  </div>
  <div class="service" style="left:201px;top:967px">
    <div class="service-head"><span class="service-icon" role="img" aria-label="Merchant cash advance icon" style="background:#6b5444"></span><span class="service-name">Merchant<br>Cash Advance</span></div>
    <p class="service-text">Lorem Ipsum is simply dummy text of the printing and typesetting industry. Lorem Ipsum has been the industry's standard dummy text ever since the 1500s, when an unknown printer</p>
  </div>
  <div class="service" style="left:475px;top:967px">
    <div class="service-head"><span class="service-icon" role="img" aria-label="Purchase order financing icon" style="background:#f3c21a"></span><span class="service-name">Purchase Order<br>Financing</span></div>
    <p class="service-text">Lorem Ipsum is simply dummy text of the printing and typesetting industry. Lorem Ipsum has been the industry's standard dummy text ever since the 1500s, when an unknown printer</p>
  </div>
  <div class="service" style="left:748px;top:967px">
    <div class="service-head"><span class="service-icon" role="img" aria-label="Asset based lending icon" style="background:#f1f1f1"></span><span class="service-name">Asset Based<br>Lending</span></div>
    <p class="service-text">Lorem Ipsum is simply dummy text of the printing and typesetting industry. Lorem Ipsum has been the industry's standard dummy text ever since the 1500s, when an unknown printer</p>
  </div>
</section>

<section class="introducers">
  <div class="intro-photo" role="img" aria-label="Red-tinted photo of business people meeting at a laptop"></div>
  <svg class="edges" width="1200" height="740" viewBox="0 0 1200 740" aria-hidden="true">
    <path d="M0 0 H1200 V10 C800 20 380 50 0 100 Z" fill="#ffffff"/>
    <path d="M0 100 C380 50 800 20 1200 10 V24 C800 36 380 70 0 120 Z" fill="#2a2a2a"/>
    <path d="M0 720 C420 690 820 650 1200 632 V612 C820 630 420 670 0 706 Z" fill="#2a2a2a"/>
    <path d="M0 720 C420 690 820 650 1200 632 V740 H0 Z" fill="#ffffff"/>
  </svg>
  <h2 class="section-title light" style="top:92px">Introducers</h2>
  <svg class="swoosh" style="top:134px" viewBox="0 0 184 16" aria-hidden="true"><path d="M2 14 C60 2 130 0 182 4 C130 4 70 7 2 14 Z" fill="#ffffff"/></svg>
  <div class="video-frame" role="img" aria-label="Video still of a smiling family outdoors">
    <span class="play"><svg width="26" height="32" viewBox="0 0 26 32"><path d="M2 2 L24 16 L2 30 Z" fill="#fff"/></svg></span>
  </div>
  <p class="intro-caption">At vero eos et accusamus et iusto odio dignissimos ducimus qui blanditiis praesentium voluptatum deleniti atque corrupti</p>
  <a class="btn" href="#">Learn More</a>
</section>

<h2 class="section-title" style="top:1874px">Testimonials</h2>
<svg class="swoosh" style="top:1916px" viewBox="0 0 184 16" aria-hidden="true"><path d="M2 14 C60 2 130 0 182 4 C130 4 70 7 2 14 Z" fill="#1d1d1d"/></svg>
<div class="quote-mark">&ldquo;</div>
<p class="testimonial-text">At vero eos et accusamus et iusto odio dignissimos ducimus qui blanditiis praesentium voluptatum deleniti atque corrupti quos dolores et quas molestias excepturi sint occaecati cupiditate non provident, similique sunt in culpa qui officia</p>
<svg class="tri" style="left:136px" width="10" height="12" viewBox="0 0 10 12" aria-hidden="true"><path d="M9 0 L0 6 L9 12 Z" fill="#b8121c"/></svg>
<svg class="tri" style="left:1054px" width="10" height="12" viewBox="0 0 10 12" aria-hidden="true"><path d="M1 0 L10 6 L1 12 Z" fill="#b8121c"/></svg>
<div class="divider"></div>
<div class="avatar" role="img" aria-label="Portrait photo of the client"></div>
<div class="author">
  <div class="author-name">Daniel Ashford</div>
  <div class="author-company">Company Name</div>
</div>

<footer class="site-footer">
  <div class="footer-bg" role="img" aria-label="Dark city skyline at night"></div>
  <svg class="edge" width="1200" height="80" viewBox="0 0 1200 80" aria-hidden="true">
    <path d="M0 0 H1200 V12 C800 48 400 54 0 22 Z" fill="#ffffff"/>
    <path d="M0 22 C400 54 800 48 1200 12 V26 C800 66 400 72 0 38 Z" fill="#b8121c"/>
  </svg>
  <div class="footer-brand"><span class="dot"></span>Merrow Trade finance</div>
  <div class="social">
    <span style="background:#3b5a9a"></span><span style="background:#3fa34d"></span><span style="background:#d0312d"></span><span style="background:#2aa9e0"></span><span style="background:#d44133"></span>
  </div>
  <div class="foot-col" style="left:401px">
    <h4>QUICK LINKS</h4>
    <ul><li>Home</li><li>About Us</li><li>Services</li><li>Introducers</li><li>Contact Us</li></ul>
  </div>
  <div class="foot-col" style="left:579px">
    <h4>OTHER LINKS</h4>
    <ul><li>Terms Of Service</li><li>Privacy Policy</li><li>Cookies</li><li>Help</li><li>Disclaimer</li></ul>
  </div>
  <div class="foot-col newsletter" style="left:760px">
    <h4><svg width="18" height="13" viewBox="0 0 18 13" style="vertical-align:-1px;margin-right:6px" aria-hidden="true"><rect x="1" y="1" width="16" height="11" fill="none" stroke="#b8121c" stroke-width="1.5"/><path d="M1 1 L9 7 L17 1" fill="none" stroke="#b8121c" stroke-width="1.5"/></svg>NEWSLETTER <em>SIGN UP</em></h4>
    <p>At vero eos et accusamus et iusto odio dignissimos ducimus qui blanditiis praesentium voluptatum</p>
    <div class="subscribe"><span class="field">Enter Your E-mail Address</span><span class="go">SUBSCRIBE NOW</span></div>
  </div>
  <div class="footer-rule"></div>
  <p class="copyright">&copy; 2016 Company Name | All Rights Reserved</p>
</footer>

</body>
</html>
```